VELMOR Website Design

We need a website designed for our company VELMOR. We are a luxury lifestyle club that will provide benefits and services for our members. The site should be clean & sleek, preferably using black and white (or darker colors). (example sites: stravenhall.example, plinth.example)

Here is a link of a sample page I did using wix. (https://dunmere7.sitehostly.example/mysite) This can be used to get a general idea.

Target Market(s)

Upper Middle Class in the United States

Number of Pages Required

5+ page

Font styles to use
Sans Serif
Other font styles liked:
• Arial (or other similar fonts)

Requirements
Must have
• A clean design that is eye-catching and speaks to our company.
Nice to have
• Ideas for copy.

```html
<!DOCTYPE html>
<html lang="en">
<head>
<meta charset="UTF-8">
<title>VELMOR — Contact</title>
<link rel="stylesheet" href="https://fonts.googleapis.com/css2?family=Montserrat:wght@400;500;600&display=swap">
<style>
  :root {
    --bg-deep: #070b17;
    --panel-a: #0b1a2a;
    --panel-b: #0c1738;
    --panel-c: #0a1230;
    --ink: #ffffff;
    --ink-soft: #d9dce4;
    --rule: #bfc3cc;
    --icon: #b9bcc4;
  }
  * { margin: 0; padding: 0; box-sizing: border-box; }
  html, body { width: 1200px; height: 976px; overflow: hidden; background: var(--bg-deep); }
  body { font-family: "Montserrat", Arial, sans-serif; color: var(--ink); position: relative; }

  .backdrop { position: absolute; inset: 0; width: 1200px; height: 976px; }

  .brand { position: absolute; left: 150px; top: 30px; font-size: 32px; font-weight: 500; letter-spacing: 1.5px; }

  .main-nav { position: absolute; top: 41px; left: 0; width: 1200px; height: 16px; }
  .main-nav a { position: absolute; font-size: 12px; letter-spacing: 0.6px; color: var(--ink-soft); text-decoration: none; white-space: nowrap; }
  .main-nav a.is-current { color: var(--ink); font-weight: 600; }

  .headline { position: absolute; left: 150px; top: 232px; font-size: 40px; font-weight: 400; letter-spacing: 0.3px; white-space: nowrap; }

  .field { position: absolute; border-bottom: 1px solid var(--rule); }
  .field span { position: absolute; left: 0; font-size: 16px; letter-spacing: 0.4px; color: var(--ink-soft); }
  .field-name { left: 150px; top: 350px; width: 218px; height: 31px; }
  .field-name span { left: 2px; top: 3px; }
  .field-email { left: 412px; top: 350px; width: 218px; height: 31px; }
  .field-email span { top: 3px; }
  .field-subject { left: 150px; top: 400px; width: 480px; height: 31px; }
  .field-subject span { top: 3px; }
  .field-message { left: 150px; top: 437px; width: 480px; height: 144px; }
  .field-message span { top: 2px; }

  .send-button { position: absolute; left: 318px; top: 612px; width: 143px; height: 44px; border: 2px solid var(--ink); border-radius: 22px; background: transparent; color: var(--ink); font-family: "Montserrat", Arial, sans-serif; font-size: 13.5px; font-weight: 600; }

  .footer-contact { position: absolute; left: 0; top: 905px; width: 1200px; text-align: center; }
  .footer-contact h2 { font-size: 12px; font-weight: 600; letter-spacing: 0.3px; }
  .social-links { display: flex; justify-content: center; gap: 13px; margin-top: 9px; }
  .social-links span { width: 14px; height: 14px; border-radius: 50%; background: var(--icon); }
</style>
</head>
<body>
  <svg class="backdrop" viewBox="0 0 1200 976" role="img" aria-label="Faceted low-poly decorative surface in deep navy and teal tones">
    <defs>
      <linearGradient id="facetTone" x1="0" y1="0" x2="1" y2="1">
        <stop offset="0" stop-color="var(--panel-a)"/>
        <stop offset="0.5" stop-color="var(--panel-b)"/>
        <stop offset="1" stop-color="var(--panel-c)"/>
      </linearGradient>
    </defs>
    <polygon points="1008,0 1200,0 1200,976 692,976 496,384" fill="url(#facetTone)"/>
  </svg>

  <div class="brand">VELMOR</div>

  <nav class="main-nav">
    <a style="left:613px">HOME</a>
    <a style="left:681px">ABOUT</a>
    <a style="left:754px">SERVICES AND BENEFITS</a>
    <a style="left:947px">APPLY</a>
    <a class="is-current" style="left:1016px">CONTACT</a>
  </nav>

  <h1 class="headline">We’re always here, drop us a line!</h1>

  <form>
    <div class="field field-name"><span>Name *</span></div>
    <div class="field field-email"><span>Email *</span></div>
    <div class="field field-subject"><span>Subject</span></div>
    <div class="field field-message"><span>Message</span></div>
    <button class="send-button" type="button">Send</button>
  </form>

  <footer class="footer-contact">
    <h2>CONTACT US</h2>
    <div class="social-links">
      <span></span><span></span><span></span><span></span><span></span>
    </div>
  </footer>
</body>
</html>
```